Small Business Consulting Firm Needs Letterhead

We need a letterhead for our company "Brightpath Plus". Our company does outbound calling and mailing to business owner's companies who have taken high interest loans. These loans tend to put these businesses in a big financial bind short term, and we help them find better financial options. We would like the design to match our colors of our logo. Headers and footers would look nice, but we are open. We would want it to include our address, website, phone, and email info. Our address - 2000 E. Lamar Blvd. Suite 600Website - www.safeguardtoday.comEmail - info@safeguardtoday.comPhone - 855-726-1938
Industry/Entity Type
Financial Planning
Look and feel
Each slider illustrates characteristics of the customer's brand and the style your logo design should communicate.

```html
<!DOCTYPE html>
<html lang="en">
<head>
<meta charset="utf-8">
<title>Brightpath Plus Letterhead</title>
<link rel="stylesheet" href="https://fonts.googleapis.com/css2?family=Didact+Gothic&family=Lato:wght@400;700&display=swap">
<style>
  :root {
    --backdrop: #cdf3df;
    --paper: #ffffff;
    --ink: #3a3a3a;
    --ink-soft: #555555;
    --brand-green: #6fb43f;
    --brand-blue: #1b7fc4;
  }
  * { margin: 0; padding: 0; box-sizing: border-box; }
  html, body {
    width: 1200px; height: 898px; overflow: hidden;
    background: var(--backdrop);
  }
  .letterhead {
    position: absolute; left: 296px; top: 19px;
    width: 608px; height: 860px;
    background: var(--paper);
    box-shadow: 0 6px 24px rgba(0,0,0,0.12);
    font-family: "Didact Gothic", sans-serif;
    color: var(--ink);
  }
  .brand {
    position: absolute; top: 96px; left: 0; right: 0;
    text-align: center;
  }
  .brand-mark {
    display: block; margin: 0 auto 16px;
    width: 26px; height: 26px; background: var(--brand-green);
  }
  .brand-name {
    font-size: 27px; letter-spacing: 3px; color: var(--ink);
    text-transform: uppercase;
  }
  .contact-band {
    position: absolute; top: 186px; left: 40px; right: 40px;
    border-top: 2px solid var(--brand-green);
    border-bottom: 2px solid var(--brand-green);
    padding: 8px 0;
    display: flex; justify-content: center; gap: 20px;
    font-family: "Lato", sans-serif; font-size: 12.5px; color: var(--ink);
  }
  .contact-item { display: flex; align-items: center; gap: 6px; }
  .contact-item svg { width: 12px; height: 12px; fill: none; stroke: var(--brand-blue); stroke-width: 1.6; }
  .letter-body {
    position: absolute; top: 268px; left: 58px; right: 58px;
    font-size: 13.5px; line-height: 1.62; color: var(--ink-soft);
  }
  .greeting { margin-bottom: 22px; font-size: 14px; color: var(--ink); }
  .letter-body p.paragraph { margin-bottom: 22px; text-align: justify; }
  .signature {
    position: absolute; top: 650px; right: 62px; text-align: right;
  }
  .signature-name { font-size: 18px; color: var(--ink); }
  .signature-title { font-size: 11.5px; color: var(--ink-soft); margin-top: 4px; }
  .footer-band {
    position: absolute; top: 756px; left: 40px; right: 40px;
    border-top: 2px solid var(--brand-blue);
    border-bottom: 2px solid var(--brand-blue);
    padding: 9px 0; text-align: center;
    font-family: "Lato", sans-serif; font-size: 12.5px; color: #222;
  }
</style>
</head>
<body>
  <main class="letterhead">
    <header class="brand">
      <span class="brand-mark" aria-hidden="true"></span>
      <div class="brand-name">Brightpath Plus</div>
    </header>

    <div class="contact-band">
      <span class="contact-item">
        <svg viewBox="0 0 12 12"><path d="M2 1.5h2.2l1 2.6-1.3 1a6 6 0 0 0 3 3l1-1.3 2.6 1v2.2c-5 .4-9-3.6-8.5-8.5z"/></svg>
        (855) 726-1938
      </span>
      <span class="contact-item">
        <svg viewBox="0 0 12 12"><rect x="1" y="2.5" width="10" height="7"/><path d="M1 2.5l5 4 5-4"/></svg>
        info@brightpathplus.com
      </span>
      <span class="contact-item">
        <svg viewBox="0 0 12 12"><circle cx="6" cy="6" r="4.8"/><path d="M1.2 6h9.6M6 1.2c-2.4 2.6-2.4 7 0 9.6M6 1.2c2.4 2.6 2.4 7 0 9.6"/></svg>
        www.brightpathplus.com
      </span>
    </div>

    <section class="letter-body">
      <p class="greeting">Hello Sir/Mam</p>
      <p class="paragraph">Lorem ipsum dolor sit amet, consectetur adipiscing elit. Donec orci purus, luctus vitae dignissim eu, iaculis sed purus. Vivamus faucibus, ipsum nec aliquet viverra, leo mauris condimentum ligula, sit amet sagittis enim ligula quis arcu. Nam egestas tortor id nisi porttitor mattis. In tortor ante, ultricies in suscipit a, tempus non massa. Vivamus et auctor mi. Fusce vel massa nulla. Phasellus nec eros mauris, et scelerisque orci. Donec malesuada orci vitae nulla accumsan porta a id massa.</p>
      <p class="paragraph">Quisque accumsan iaculis magna sit amet fringilla. Maecenas consequat, magna eget tincidunt semper, odio nibh rutrum mi, id feugiat ante nisi eu risus. Vestibulum nunc orci, rhoncus a placerat in, ultricies in mi. Cras mattis varius eros, vel fringilla nisi suscipit eget. Quisque scelerisque sagittis nulla at porttitor. Mauris a justo et tellus interdum tristique. Sed id augue vitae urna euismod commodo et aliquet a quam. Pellentesque arcu velit, cursus et malesuada ut, consequat et diam. Nullam erat sem, rhoncus id ullamcorper vitae, rhoncus et arcu. In ultricies nulla.</p>
    </section>

    <div class="signature">
      <div class="signature-name">Dana Whitfield</div>
      <div class="signature-title">Co-Founder &amp; CEO</div>
    </div>

    <footer class="footer-band">4170 W. Corwin Ave. Suite 310, Millbrook, Carver County 75021, USA</footer>
  </main>
</body>
</html>
```